Rebrand stationary with recently completed logo design

Need new business cards, thank you cards, letterhead, envelopes and presentation folders. The designs will be sent to a separate production firm so I need the files to be print ready.

My contact info
Reko Haliburn

Office 604-318-5047
Fax 604-371-8054

Email reko@glazemark.ca
website www.glazemark.ca

315-14720 62nd Avenue,
Langley, BC, V2K 3R8

Target Market(s)

Homeowners, businesses and contractors

Industry/Entity Type

Business

Font styles to use
Sans Serif

Colors
34a7d7

Requirements
Must have
• Like to have one side of the business card a solid color with the logo in all white. The side with all the text to be a white background
• I find the current blue on the front of the card with the white logo too dark.
Should not have
• Gradient colors

```html
<!DOCTYPE html>
<html lang="en">
<head>
<meta charset="utf-8">
<title>Glazemark Business Card</title>
<link href="https://fonts.googleapis.com/css2?family=Open+Sans:wght@400;600;700&family=PT+Sans+Narrow:wght@700&display=swap" rel="stylesheet">
<style>
  :root {
    --page-bg: #e4e1dc;
    --card-white: #f7f7f7;
    --brand-blue: #34a7d7;
    --slate: #3d4b55;
    --text-grey: #4a4f54;
    --white: #ffffff;
  }
  * { margin: 0; padding: 0; box-sizing: border-box; }
  html, body {
    width: 1200px; height: 960px; overflow: hidden;
    background: var(--page-bg);
    font-family: "Open Sans", sans-serif;
  }
  .canvas { position: relative; width: 1200px; height: 960px; }

  .card {
    position: absolute; width: 600px; height: 342px;
    box-shadow: 0 3px 8px rgba(0,0,0,0.25);
  }
  .card--front { left: 302px; top: 129px; background: var(--card-white); }
  .card--back  { left: 299px; top: 488px; background: var(--slate); }

  .wordmark {
    position: absolute; font-weight: 400; letter-spacing: -0.5px; line-height: 1;
  }
  .card--front .wordmark { left: 46px; top: 54px; font-size: 42px; color: var(--slate); }

  .address {
    position: absolute; left: 47px; top: 172px;
    font-size: 13px; line-height: 18px; color: var(--text-grey); font-style: normal;
  }
  .contact-list {
    position: absolute; left: 47px; top: 218px; list-style: none;
    font-size: 13px; color: var(--text-grey);
  }
  .contact-list li { display: flex; align-items: center; height: 19.5px; }
  .contact-list svg { width: 14px; height: 12px; margin-right: 8px; fill: var(--brand-blue); }
  .website {
    position: absolute; left: 47px; top: 280px;
    font-size: 13px; font-weight: 700; color: var(--brand-blue);
  }

  .name-mark {
    position: absolute; left: 367px; top: 210px; width: 26px; height: 26px;
    background: var(--slate);
  }
  .name-band {
    position: absolute; left: 397px; top: 215px; width: 203px; height: 39px;
    background: var(--brand-blue);
    display: flex; align-items: center; justify-content: center;
  }
  .name-band span {
    font-family: "PT Sans Narrow", sans-serif; font-weight: 700;
    font-size: 20px; color: var(--white); text-transform: uppercase; letter-spacing: 0.2px;
  }

  .back-mark {
    position: absolute; left: 125px; top: 108px; width: 60px; height: 120px;
    display: flex; align-items: center;
  }
  .back-mark::before {
    content: ""; display: block; width: 58px; height: 58px; background: var(--white);
  }
  .card--back .wordmark { left: 199px; top: 146px; font-size: 44px; color: var(--white); }
</style>
</head>
<body>
<main class="canvas">

  <section class="card card--front" aria-label="Business card front">
    <div class="wordmark">GLAZEMARK</div>

    <address class="address">
      315-14720 62nd Avenue<br>
      Langley, BC, V2K 3R8
    </address>

    <ul class="contact-list">
      <li>
        <svg viewBox="0 0 14 14" aria-hidden="true"><path d="M3 0.5 5.2 3.2 4 5a8 8 0 0 0 5 5l1.8-1.2 2.7 2.2-1.6 2.3C6 13 1 8 0.7 2.1Z"/></svg>
        604-318-5047
      </li>
      <li>
        <svg viewBox="0 0 14 12" aria-hidden="true"><rect x="3" y="0" width="8" height="4"/><rect x="0" y="5" width="14" height="5" rx="1"/><rect x="3" y="9" width="8" height="3"/></svg>
        604-371-8054
      </li>
      <li>
        <svg viewBox="0 0 14 10" aria-hidden="true"><path d="M0 1 7 6 14 1V10H0Z"/><path d="M0 0H14L7 5Z"/></svg>
        reko@glazemark.ca
      </li>
    </ul>

    <div class="website">www.glazemark.ca</div>

    <div class="name-mark" aria-hidden="true"></div>
    <div class="name-band"><span>Reko Haliburn</span></div>
  </section>

  <section class="card card--back" aria-label="Business card back">
    <div class="back-mark" aria-hidden="true"></div>
    <div class="wordmark">GLAZEMARK</div>
  </section>

</main>
</body>
</html>
```